Vernac Law Business cards and stationary design project

We are looking for a stationary design for business cards (double sided), 8x10, 5x7, and legal and standard envelopes.

We would like the design to match the logo that we have already.
Color palate preferred is Teal, White, grey and any others that will look good for a professional law firm.

We would like this statement: "RELATIONSHIPS. RESPECT. RESULT" to be on the back of the business cards and maybe on the stationary if it looks good.

Please see link to website for more information: www.vernac-law.example

Target Market(s)

Potential clients that need Attorney services.

Industry/Entity Type

Law Firm

Contact Information for Business Card

We would like the front and back to be two different colors. Current business cards are teal front, grey back and are a vertical design. We are open to options with colors.

Font styles to use
Serif

Colors
33a6d7
33b8a4
b9b9b9
5c5c5c

Requirements
Must have
• Logo supplied needs to go on the card and stationary.
• Match website color palate, www.vernac-law.example
• Be professional and not too wordy.
• Criminal Law, Civil Litigation, Personal Injury, Restraining Orders need to be on the card.
Nice to have
• COUNSEL. CLARITY. COMMITMENT. on the back of the card.
Should not have
• Not be too busy/wordy or too flashy.

```html
<!DOCTYPE html>
<html lang="en">
<head>
<meta charset="utf-8">
<title>Vernac Law – Business Card</title>
<link rel="stylesheet" href="https://fonts.googleapis.com/css2?family=Cinzel:wght@400;500&family=Tinos&display=swap">
<style>
  :root {
    --teal: #128896;
    --teal-back: #108896;
    --ink: #555555;
    --white: #ffffff;
    --backdrop: #4a4a4a;
    --display: "Cinzel", serif;
    --body: "Tinos", serif;
  }
  * { box-sizing: border-box; margin: 0; padding: 0; }
  html, body { width: 1105px; height: 1200px; overflow: hidden; }
  body { background: var(--backdrop); position: relative; }

  .card {
    position: absolute;
    left: 196px;
    width: 719px;
    height: 410px;
    box-shadow: 0 4px 10px rgba(0,0,0,0.45);
  }
  .card--front { top: 146px; background: var(--white); }
  .card--back { top: 602px; background: var(--teal-back); }

  /* Front */
  .brand {
    position: absolute;
    right: 36px;
    top: 132px;
    display: flex;
    align-items: center;
    gap: 12px;
    font-family: var(--display);
    font-size: 30px;
    color: var(--teal);
    letter-spacing: 1px;
  }
  .brand__mark { width: 12px; height: 12px; background: var(--teal); }

  .name-tab {
    position: absolute;
    left: 0;
    top: 212px;
    width: 11px;
    height: 58px;
    background: var(--teal);
    border-radius: 0 6px 6px 0;
  }
  .holder__name {
    position: absolute;
    left: 37px;
    top: 208px;
    font-family: var(--display);
    font-weight: 500;
    font-size: 31px;
    color: var(--teal);
    letter-spacing: 1px;
  }
  .holder__title {
    position: absolute;
    left: 37px;
    top: 250px;
    right: 36px;
    display: flex;
    align-items: flex-end;
    gap: 8px;
    font-family: var(--display);
    font-size: 20px;
    color: var(--ink);
    letter-spacing: 1px;
  }
  .holder__rule { flex: 1; height: 1.5px; background: var(--teal); margin-bottom: 5px; }

  .contact {
    position: absolute;
    left: 37px;
    top: 296px;
    list-style: none;
    font-family: var(--body);
    font-size: 20px;
    color: var(--ink);
  }
  .contact li { display: flex; align-items: center; gap: 16px; height: 30.5px; }
  .contact svg { width: 18px; height: 18px; fill: var(--teal); flex: none; }

  .practice {
    position: absolute;
    right: 36px;
    top: 302px;
    list-style: none;
    text-align: right;
    font-family: var(--body);
    font-size: 20px;
    color: var(--ink);
    line-height: 26.5px;
  }

  /* Back */
  .back-brand {
    position: absolute;
    left: 0; right: 0;
    top: 168px;
    text-align: center;
    font-family: var(--display);
    font-size: 58px;
    color: var(--white);
    letter-spacing: 2px;
  }
  .tagline {
    position: absolute;
    left: 0; right: 0;
    top: 356px;
    text-align: center;
    font-family: var(--display);
    font-size: 21px;
    color: var(--white);
    letter-spacing: 1px;
  }
</style>
</head>
<body>

<section class="card card--front" aria-label="Business card front">
  <div class="brand"><span class="brand__mark"></span><span>Vernac Law</span></div>

  <div class="name-tab"></div>
  <h1 class="holder__name">Mara Vernac</h1>
  <div class="holder__title"><span>Trial Lawyer</span><span class="holder__rule"></span></div>

  <ul class="contact">
    <li>
      <svg viewBox="0 0 24 24" aria-hidden="true"><path d="M6.6 10.8c1.4 2.8 3.8 5.1 6.6 6.6l2.2-2.2c.3-.3.7-.4 1-.2 1.1.4 2.3.6 3.6.6.6 0 1 .4 1 1V20c0 .6-.4 1-1 1C10.6 21 3 13.4 3 4c0-.6.4-1 1-1h3.5c.6 0 1 .4 1 1 0 1.3.2 2.5.6 3.6.1.3 0 .7-.2 1l-2.3 2.2z"/></svg>
      <span>(555) 014-2870</span>
    </li>
    <li>
      <svg viewBox="0 0 24 24" aria-hidden="true"><path d="M2 5h20v14H2z"/><path d="M2 5l10 7 10-7" fill="none" stroke="#fff" stroke-width="1.8"/></svg>
      <span>mara@vernac-law.example</span>
    </li>
    <li>
      <svg viewBox="0 0 24 24" aria-hidden="true"><circle cx="12" cy="12" r="10"/><path d="M7 7c2 0 3 1 3 2.5S8 11 8 13s2 2 2 4M14 4c0 2 2 2 3 3s-1 3 1 4 3 0 3 0M13 20c0-2 1-3 3-3" fill="none" stroke="#fff" stroke-width="1.6"/></svg>
      <span>www.vernac-law.example</span>
    </li>
  </ul>

  <ul class="practice">
    <li>Criminal Law</li>
    <li>Civil Litigation/Personal Injury</li>
    <li>Restraining</li>
  </ul>
</section>

<section class="card card--back" aria-label="Business card back">
  <div class="back-brand">Vernac Law</div>
  <p class="tagline">COUNSEL. CLARITY. COMMITMENT.</p>
</section>

</body>
</html>
```